CoinHarbor.com Site Redesign

We are looking to redesign our CoinHarbor.com site. This site is focused on helping consumers make smart financial decisions. We provide reviews and articles in various categories.

We are looking for a responsive design to run on wordpress. We will also have adsense advertisements on our page and will want some ad spot space. We are thinking of two column design vs. single column.

Here is an example of what our competitors look like:
ShopperBeacon.org (mostly reviews vs. articles)
Homepage - https://www.shopperbeacon.example/
Category Review Listing - https://www.shopperbeacon.example/mortgage-refinance/best-mortgage-refinance
Individual Review - https://www.shopperbeacon.example/mortgage-refinance/c/loan-orchard-mortgage-refinance-review

- I like that the site is extremely clean. I like the fixed header in mobile

PilotGuide
Homepage - https://www.pilotguide.example/
Category Review Listing-https://www.pilotguide.example/auto_insurance/index.php
Individual Review- https://www.pilotguide.example/auto_insurance/drivora_review.php

Articles - https://www.pilotguide.example/blog/2017/11/20/going-on-a-holiday-road-trip-be-prepared-for-these-hazards/

What I Like? I like the two column layout in that it gives room for advertising.
What I Do NOT Like? The top navigation is a little cumbersome and old. Mobile view is not very good. Content seems a bit cluttered.

PennyMoth
Homepage - https://www.pennymoth.example
Category Review Listing - https://www.pennymoth.example/blog/insurance/best-car-insurance-companies/?trk=pm_gn1_4.0
Individual Review- https://www.pennymoth.example/blog/insurance/veloro-insurance-review/

What I Like? very clean. Like the use of white space and focus on bright color call to action buttons.
What I Do NOT Like? In mobile a lot of content is pushed below the fold because of the large image above the fold. Reviews are not well organized.

Target Market(s)

consumers interested in saving money and making smart financial decisions

Industry/Entity Type

Financial

Logo Text

CoinHarbor.com or CoinHarbor

Coding

Coded - Design and coding required

Number of Pages Required

5+ page

Font styles to use
Sans Serif

Colors

Designer to choose colors to be used in the design.

Requirements
Must have
• -responsive design
• -room for ad space in the right column
Nice to have
• -good use of white space
• -clean layouts
Should not have
• -clutter

```html
<!DOCTYPE html>
<html lang="en">
<head>
<meta charset="utf-8">
<title>CoinHarbor</title>
<link rel="stylesheet" href="https://fonts.googleapis.com/css2?family=Lato:ital,wght@0,400;0,700;0,900;1,400&display=swap">
<style>
:root{
  --purple:#6a2fc0;
  --violet:#8a37c9;
  --magenta:#b23bb8;
  --orange:#ff8a00;
  --orange-deep:#f27a12;
  --ink:#2d2d3a;
  --muted:#6f6f7a;
  --light:#eeeeef;
  --line:#d9d9de;
  --white:#ffffff;
}
*{box-sizing:border-box;margin:0;padding:0}
html,body{width:1200px;height:2200px;overflow:hidden}
body{font-family:"Lato",Arial,sans-serif;color:var(--ink);background:var(--white)}
a{color:inherit;text-decoration:none}

.site-header{height:110px;display:flex;align-items:center;justify-content:space-between;padding:0 44px;background:var(--white)}
.brand{font-size:34px;font-weight:900;color:var(--purple)}
.main-nav{display:flex;gap:34px;font-size:19px;color:var(--muted)}

.hero{position:relative;height:442px}
.hero-photo{position:absolute;inset:0;background:linear-gradient(100deg,#b9b4ad 0%,#8e8b86 35%,#5f5d5d 70%,#7d7a76 100%)}
.hero-photo::after{content:"";position:absolute;inset:0;background:rgba(40,30,60,.35)}
.category-grid{position:absolute;left:132px;top:58px;width:936px;display:grid;grid-template-columns:repeat(4,1fr);gap:12px}
.category-tile{height:168px;border:2px solid rgba(255,255,255,.8);display:flex;flex-direction:column;align-items:center;justify-content:center;gap:18px;color:var(--white);font-size:16px;font-weight:700;letter-spacing:.5px;text-transform:uppercase;background:rgba(255,255,255,.06)}
.category-tile.is-active{background:linear-gradient(135deg,var(--purple),var(--magenta));border-color:transparent}
.category-tile svg{width:64px;height:56px;fill:none;stroke:#fff;stroke-width:3;stroke-linejoin:round;stroke-linecap:round}

.search-bar{position:relative;z-index:2;margin:-4px auto 0;width:960px;height:100px;background:linear-gradient(90deg,var(--violet),var(--magenta) 60%,#c2479e);display:flex;align-items:center;justify-content:center;gap:30px}
.search-bar label{color:var(--white);font-size:27px}
.search-field{width:376px;height:50px;background:var(--white);display:flex;align-items:center;justify-content:space-between;padding:0 18px;color:#999;font-size:18px}
.search-field svg{width:14px;height:10px;fill:#888}

.why-choose{background:var(--light);margin-top:-50px;padding:110px 120px 60px;display:flex;justify-content:space-between;height:480px}
.why-choose .copy{width:470px}
.section-title{font-size:36px;color:var(--purple);font-weight:400;margin-bottom:24px}
.why-choose p{font-size:16px;line-height:1.6;color:var(--muted);margin-bottom:14px}
.btn{display:inline-block;background:var(--orange);color:var(--white);font-weight:700;font-size:16px;padding:12px 30px;border-radius:26px;margin-top:10px}
.media-placeholder{width:400px;height:290px;margin-top:-10px;background:linear-gradient(135deg,#e4e6ea,#c9cdd4)}

.testimonial{margin-top:48px;height:304px;background:linear-gradient(100deg,var(--purple) 0%,var(--magenta) 45%,var(--orange) 100%);display:flex;align-items:center;justify-content:center;gap:40px;position:relative}
.arrow{position:absolute;top:50%;width:24px;height:36px;margin-top:-18px;fill:none;stroke:#fff;stroke-width:4}
.arrow.prev{left:140px}.arrow.next{right:140px}
.avatar{width:136px;height:136px;border-radius:50%;border:4px solid rgba(255,255,255,.8);background:linear-gradient(160deg,#8a6a5a,#3b2c2c)}
.quote{width:520px;color:var(--white)}
.quote blockquote{font-style:italic;font-size:21px;line-height:1.45}
.quote cite{display:block;margin-top:18px;font-style:normal;font-size:15px;opacity:.9}

.why-check{padding:48px 0 0;text-align:center;height:340px}
.why-check .section-title{font-size:30px;margin-bottom:44px}
.features{display:flex;justify-content:center;gap:60px}
.feature{display:flex;gap:16px;width:260px;text-align:left}
.feature-icon{flex:none;width:72px;height:72px;border-radius:50%;background:#f6b400;border:6px solid #fde3a0;display:flex;align-items:center;justify-content:center}
.feature-icon svg{width:34px;height:34px;fill:var(--purple)}
.feature h3{font-size:18px;font-weight:900;margin-bottom:8px}
.feature p{font-size:14px;line-height:1.5;color:var(--muted)}

.newsletter{background:var(--light);height:260px;text-align:center;padding-top:52px}
.newsletter h2{font-size:36px;font-weight:400;color:var(--purple)}
.newsletter p{font-size:17px;color:var(--muted);margin:10px 0 30px}
.subscribe{display:inline-flex;width:560px;height:52px;background:var(--white);border-radius:28px;align-items:center;padding:0 6px 0 24px;justify-content:space-between}
.subscribe span{display:flex;align-items:center;gap:12px;color:#999;font-size:17px}
.subscribe svg{width:20px;height:14px;fill:none;stroke:#999;stroke-width:2}
.subscribe b{background:var(--orange-deep);color:var(--white);padding:12px 30px;border-radius:24px;font-size:16px}

.site-footer{background:var(--white);text-align:center;padding-top:50px}
.footer-nav{display:flex;justify-content:center;gap:26px;font-size:17px}
.copyright{font-size:13px;color:var(--muted);margin:14px 0 16px}
.social{display:flex;justify-content:center;gap:10px}
.social i{width:30px;height:30px;border-radius:50%;background:var(--purple)}
.social i:nth-child(2){background:#5a8fd8}
.social i:nth-child(3){background:#d9473b}
.social i:nth-child(4){background:#2f6ea8}
.social i:nth-child(5){background:#d8322d}
</style>
</head>
<body>
<header class="site-header">
  <a class="brand" href="#">CoinHarbor</a>
  <nav class="main-nav"><a>Home</a><a>About Us</a><a>Services</a><a>Products</a><a>Why Us</a><a>Testimonials</a><a>Contact Us</a></nav>
</header>

<section class="hero">
  <div class="hero-photo" role="img" aria-label="Photo of a person working at a laptop at a desk"></div>
  <div class="category-grid">
    <a class="category-tile is-active"><svg viewBox="0 0 64 56"><rect x="4" y="10" width="56" height="36" rx="4"/><line x1="4" y1="20" x2="60" y2="20"/><line x1="12" y1="36" x2="28" y2="36"/></svg>Credit Cards</a>
    <a class="category-tile"><svg viewBox="0 0 64 56"><path d="M6 28 32 6l26 22"/><path d="M14 22v28h36V22"/><rect x="27" y="34" width="10" height="16"/></svg>Mortgages</a>
    <a class="category-tile"><svg viewBox="0 0 64 56"><path d="M6 40h14l10 6 24-12-4-4-14 6"/><circle cx="36" cy="16" r="10"/></svg>Loans</a>
    <a class="category-tile"><svg viewBox="0 0 64 56"><rect x="10" y="16" width="44" height="34" rx="3"/><path d="M20 16V10h24v6"/><circle cx="32" cy="33" r="7"/></svg>Saving Accounts</a>
    <a class="category-tile"><svg viewBox="0 0 64 56"><path d="M6 32l50-18-10 30-12-8-6 10-2-12z"/></svg>Travel Money</a>
    <a class="category-tile"><svg viewBox="0 0 64 56"><circle cx="32" cy="18" r="10"/><path d="M12 52c2-12 10-18 20-18s18 6 20 18z"/></svg>Current Accounts</a>
    <a class="category-tile"><svg viewBox="0 0 64 56"><path d="M6 38l6-14h40l6 14v8H6z"/><circle cx="18" cy="46" r="5"/><circle cx="46" cy="46" r="5"/></svg>Car Insurance</a>
    <a class="category-tile"><svg viewBox="0 0 64 56"><path d="M8 48 24 30l10 10 22-24"/><path d="M44 16h12v12"/></svg>Investments</a>
  </div>
</section>

<div class="search-bar">
  <label>Looking for Something else?</label>
  <div class="search-field">I want to check<svg viewBox="0 0 14 10"><path d="M0 0h14L7 10z"/></svg></div>
</div>

<section class="why-choose">
  <div class="copy">
    <h2 class="section-title">Why Choose us</h2>
    <p>Lorem ipsum dolor sit amet consectetur adipiscing elit sed do eiusmod tempor incididunt ut labore et dolore magna aliqua ut enim ad minim veniam quis nostrud exercitation.</p>
    <p>Duis aute irure dolor in reprehenderit in voluptate velit esse cillum dolore eu fugiat nulla pariatur excepteur sint.</p>
    <a class="btn">Read More</a>
  </div>
  <div class="media-placeholder" role="img" aria-label="Illustration of a desktop computer showing a financial chart"></div>
</section>

<section class="testimonial">
  <svg class="arrow prev" viewBox="0 0 24 36"><path d="M20 2 4 18l16 16"/></svg>
  <div class="avatar" role="img" aria-label="Portrait of the client"></div>
  <div class="quote">
    <blockquote>“ Nulla sit amet diam quis non nunc rhoncus dictum metus. Curabitur tristique est condimentum orci. Phasellus pellentesque aliquam enim. Proin dui lectus cursus ”</blockquote>
    <cite>By Author Name</cite>
  </div>
  <svg class="arrow next" viewBox="0 0 24 36"><path d="M4 2l16 16L4 34"/></svg>
</section>

<section class="why-check">
  <h2 class="section-title">Why Check with us?</h2>
  <div class="features">
    <div class="feature">
      <div class="feature-icon"><svg viewBox="0 0 24 24"><path d="M9 16.2 4.8 12l-1.4 1.4L9 19 21 7l-1.4-1.4z"/></svg></div>
      <div><h3>TITLE GOES HERE</h3><p>Lorem ipsum is simply dummy text of the printing and typesetting industry since the 1500s.</p></div>
    </div>
    <div class="feature">
      <div class="feature-icon"><svg viewBox="0 0 24 24"><path d="M2 21h4V9H2zm20-11c0-1.1-.9-2-2-2h-6.3l1-4.6L13.6 2 7 8.6V21h11c.8 0 1.5-.5 1.8-1.2L22 13z"/></svg></div>
      <div><h3>TITLE GOES HERE</h3><p>Lorem ipsum is simply dummy text of the printing and typesetting industry since the 1500s.</p></div>
    </div>
    <div class="feature">
      <div class="feature-icon"><svg viewBox="0 0 24 24"><path d="M3 20h18v2H3zM5 12h3v6H5zm5-4h3v10h-3zm5-5h3v15h-3z"/></svg></div>
      <div><h3>TITLE GOES HERE</h3><p>Lorem ipsum is simply dummy text of the printing and typesetting industry since the 1500s.</p></div>
    </div>
  </div>
</section>

<section class="newsletter">
  <h2>Get latest Updates &amp; Newsletters</h2>
  <p>Arcu nonummy luctus dictum eget fermentum et lorem</p>
  <div class="subscribe"><span><svg viewBox="0 0 20 14"><rect x="1" y="1" width="18" height="12"/><path d="M1 1l9 7 9-7"/></svg>Email address</span><b>Subscribe</b></div>
</section>

<footer class="site-footer">
  <nav class="footer-nav"><a>Home</a><a>About Us</a><a>Services</a><a>Products</a><a>Why Us</a><a>Testimonials</a><a>Contact Us</a></nav>
  <p class="copyright">© 2018 Company Name. All rights reserved. Terms of Use.</p>
  <div class="social"><i></i><i></i><i></i><i></i><i></i></div>
</footer>
</body>
</html>
```